New Business Card Design Project LORVANTI-Italy

we are LORVANTI-Italy
our company in the market for 3 years we are luxury cosmetic company and its about time for a facelift :)
i will like to have elegant luxurious and unique business card
that will give the person that get it a unique, luxurious and elegant impression
I'm VERY OPEN FOR NEW IDEAS , even duo i add a few files of things that i see on line and i like them

i add my logo as well
my website is LORVANTI.COM
(if you would like to see the main style that we have)

Target Market(s)

adult that have money :)

Industry/Entity Type

Business

Contact Information for Business Card

Name - Dario Lorvanti
Position - CEO and CO Founder
address - 4817 E Halvern
telephone - 555-384-1926
email - dario@lorvanti.com
fax - 555-384-1926
website - LORVANTI.COM

Colors
000000
959595
fbee3e
ffffff

Requirements
Must have
• big logo in GOLD color
• elegant look
• impressive
Nice to have
• not must but maybe classy pattern background
• not must but maybe emblem
• maybe clear plastic business card
Should not have
• colors
• images

```html
<!DOCTYPE html>
<html lang="en">
<head>
<meta charset="utf-8">
<title>LORVANTI-Italy Business Card</title>
<link rel="stylesheet" href="https://fonts.googleapis.com/css2?family=EB+Garamond:wght@400;600&display=swap">
<style>
  :root {
    --bg: #141414;
    --card: #0c0c0c;
    --card-edge: #1d1d1d;
    --gold: #d2a63c;
    --white: #f2f2f2;
  }
  * { box-sizing: border-box; margin: 0; padding: 0; }
  html, body {
    width: 1200px; height: 833px; overflow: hidden;
    background: var(--bg);
    font-family: "EB Garamond", "Times New Roman", serif;
  }
  .stage { position: relative; width: 1200px; height: 833px; }
  .card {
    position: absolute;
    top: 268px;
    width: 520px; height: 297px;
    background: var(--card);
    border: 1px solid var(--card-edge);
    box-shadow: 0 12px 30px rgba(0,0,0,.6);
  }
  .card--front { left: 50px; }
  .card--back { left: 630px; }

  .brand {
    position: absolute;
    display: flex; flex-direction: column; align-items: center;
    color: var(--gold);
  }
  .brand__circle {
    width: 76px; height: 76px;
    border: 3px solid var(--gold);
    border-radius: 50%;
    margin-bottom: 14px;
  }
  .brand__name {
    font-size: 46px; font-weight: 400; letter-spacing: 1px; line-height: 1;
  }
  .card--front .brand { left: 0; right: 0; top: 72px; }
  .card--back .brand { left: 30px; width: 250px; top: 82px; }
  .card--back .brand__circle { width: 62px; height: 62px; margin-bottom: 12px; }
  .card--back .brand__name { font-size: 38px; }

  .divider {
    position: absolute; left: 292px; top: 58px;
    width: 2px; height: 180px; background: var(--gold);
  }
  .contact {
    position: absolute; left: 312px; top: 60px;
    color: var(--white); font-size: 14px; line-height: 1.25;
  }
  .contact__name { color: var(--gold); font-size: 21px; font-weight: 600; }
  .contact__role { margin-bottom: 8px; font-size: 15px; }
  .contact__company { color: var(--gold); font-weight: 600; font-size: 15px; }
  .contact__address { margin-bottom: 10px; font-size: 15px; }
  .contact__line { display: flex; align-items: center; gap: 7px; font-size: 15px; }
  .contact__line svg { width: 13px; height: 13px; fill: var(--gold); flex: none; }
  .contact__line.web { text-transform: uppercase; }
</style>
</head>
<body>
<main class="stage">
  <section class="card card--front">
    <div class="brand">
      <span class="brand__circle"></span>
      <span class="brand__name">LORVANTI</span>
    </div>
  </section>

  <section class="card card--back">
    <div class="brand">
      <span class="brand__circle"></span>
      <span class="brand__name">LORVANTI</span>
    </div>
    <span class="divider"></span>
    <div class="contact">
      <p class="contact__name">Dario Lorvanti</p>
      <p class="contact__role">CEO and CO Founder</p>
      <p class="contact__company">LORVANTI-Italy</p>
      <p class="contact__address">4817 E Halvern</p>
      <p class="contact__line">
        <svg viewBox="0 0 16 16" aria-hidden="true"><path d="M3 1l3 3-1.5 2a9 9 0 005.5 5.5L12 10l3 3-2 2C7 15 1 9 1 3z"/></svg>555-384-1926
      </p>
      <p class="contact__line">
        <svg viewBox="0 0 16 16" aria-hidden="true"><path d="M4 1h8v4H4zM1 6h14v6h-3v3H4v-3H1zm4 5v3h6v-3z"/></svg>555-384-1926
      </p>
      <p class="contact__line">
        <svg viewBox="0 0 16 16" aria-hidden="true"><path d="M1 3h14v10H1zm1.5 1.2L8 8.5l5.5-4.3z"/></svg>dario@lorvanti.com
      </p>
      <p class="contact__line web">
        <svg viewBox="0 0 16 16" aria-hidden="true"><path d="M8 1a7 7 0 110 14A7 7 0 018 1zm0 1.5C6.8 3.8 6.2 5.6 6.1 7.3h3.8C9.8 5.6 9.2 3.8 8 2.5zM2.6 7.3h2.2c.1-1.6.5-3.1 1.2-4.3a5.6 5.6 0 00-3.4 4.3zm8.6 0h2.2A5.6 5.6 0 0010 3c.7 1.2 1.1 2.7 1.2 4.3zM2.6 8.7A5.6 5.6 0 006 13c-.7-1.2-1.1-2.7-1.2-4.3zm3.5 0c.1 1.7.7 3.5 1.9 4.8 1.2-1.3 1.8-3.1 1.9-4.8zm5.1 0c-.1 1.6-.5 3.1-1.2 4.3a5.6 5.6 0 003.4-4.3z"/></svg>LORVANTI.COM
      </p>
    </div>
  </section>
</main>
</body>
</html>
```